Wordpress theme website for professionals working together

My partner and I are offering business services, my wife in the energy business as mainly as member of the board of commissioners. I am working as interim manager/consultant in the accounting and finance area. Both activities are connected in one company VELMOT BV (dutch ltd). We need a CV based website. Beside this we do some financial and accounting services.

Target Market(s)

small medium business

Font styles to use
Sans Serif

Colors

Designer to choose colors to be used in the design.

Requirements
Must have
• Pictures of both members.
• CLEAN AND SIMPLE
• I LIKE BLACK & WHITE
Nice to have
• I like design like this theme: http://theme.pruxelo-example.com/resume/

```html
<!DOCTYPE html>
<html lang="en">
<head>
<meta charset="utf-8">
<title>VELMOT BV – Resume</title>
<link rel="stylesheet" href="https://fonts.googleapis.com/css2?family=Montserrat:wght@400;500;600;700&family=Poppins:wght@400;500;600;700&display=swap">
<style>
  :root {
    --red: #d24d4d;
    --red-deep: #b83a3a;
    --maroon: #5a0505;
    --ink: #333333;
    --ink-soft: #555555;
    --grey-band: #efefef;
    --track: #e2e2e2;
    --rule: #dddddd;
    --dark-badge: #2e2e2e;
    --ring: #5c5557;
    --white: #ffffff;
  }
  * { box-sizing: border-box; margin: 0; padding: 0; }
  html, body { width: 1200px; height: 2332px; overflow: hidden; }
  body {
    position: relative;
    background: var(--white);
    font-family: "Montserrat", sans-serif;
    color: var(--ink);
  }
  .abs { position: absolute; }

  .top-band { left: 0; top: 0; width: 1200px; height: 575px; background: var(--grey-band); }

  .site-logo { left: 112px; top: 38px; font: 700 26px/30px "Montserrat", sans-serif; color: var(--ink); letter-spacing: .5px; }
  .main-nav { right: 112px; top: 42px; display: flex; gap: 46px; list-style: none; }
  .main-nav li { font: 500 15px/20px "Montserrat", sans-serif; color: var(--ink); }

  .hero-panel { left: 112px; top: 101px; width: 976px; height: 474px; background: var(--red); }
  .hero-chevron { left: 112px; top: 572px; }

  .portrait {
    left: 147px; top: 139px; width: 396px; height: 396px; border-radius: 50%;
    border: 5px solid #f0a6a6;
    background: radial-gradient(circle at 55% 45%, #c9a28c 0%, #7a5648 45%, #3a2a26 100%);
  }

  .profile-toggle {
    left: 597px; top: 171px; width: 199px; height: 47px; border-radius: 24px;
    border: 3px solid var(--white); display: flex; overflow: hidden; background: var(--white);
  }
  .profile-toggle span { flex: 1; display: flex; align-items: center; justify-content: center; font: 600 18px "Poppins", sans-serif; }
  .profile-toggle .off { color: var(--red); }
  .profile-toggle .on { background: linear-gradient(#b53535, #8e1f1f); color: var(--white); border-radius: 0 22px 22px 0; }

  .profile-info { left: 600px; top: 246px; width: 430px; color: var(--white); font-family: "Poppins", sans-serif; }
  .profile-info .name { font-size: 20px; font-weight: 500; line-height: 30px; }
  .profile-info .name b, .profile-info .jobs-title { font-weight: 700; }
  .profile-info .jobs-title { font-size: 21px; margin-top: 16px; line-height: 30px; }
  .profile-info .job { font-size: 15px; font-weight: 600; line-height: 22px; margin-top: 14px; }
  .profile-info .job b { font-weight: 700; }

  .social-list { left: 599px; top: 476px; display: flex; gap: 10px; list-style: none; }
  .social-list li { width: 42px; height: 42px; border-radius: 50%; background: var(--white); display: flex; align-items: center; justify-content: center; }
  .social-list li i { width: 8px; height: 8px; border-radius: 50%; background: var(--ink); display: block; }

  .section-title { font: 700 28px/34px "Poppins", sans-serif; color: var(--red); }
  .about-title { left: 112px; top: 735px; }
  .about-text { left: 112px; top: 786px; width: 488px; font-size: 13.5px; line-height: 24.5px; color: var(--ink-soft); text-align: justify; }
  .read-more { left: 112px; top: 933px; width: 110px; height: 46px; border: 2px solid var(--red); border-radius: 23px; color: var(--red); font-size: 14px; font-weight: 500; display: flex; align-items: center; justify-content: center; }

  .finished-jobs { left: 668px; top: 744px; width: 420px; font-family: "Montserrat", sans-serif; }
  .finished-jobs .item { margin-bottom: 26px; }
  .finished-jobs h4 { font-size: 19px; font-weight: 600; color: var(--ink); line-height: 26px; }
  .finished-jobs h4 em { font-style: normal; color: var(--red); font-weight: 700; }
  .finished-jobs p { font-size: 17px; font-weight: 500; color: var(--ink-soft); line-height: 28px; }

  .rule { left: 112px; width: 976px; height: 1px; background: var(--rule); }

  .centered-title { left: 0; width: 1200px; text-align: center; }

  .skill { width: 452px; }
  .skill .label { font: 400 19px/24px "Poppins", sans-serif; color: var(--ink); }
  .skill .track { position: relative; margin-top: 20px; height: 9px; border-radius: 5px; background: var(--track); }
  .skill .fill { position: absolute; left: 0; top: 0; height: 9px; border-radius: 5px; background: var(--red); }
  .skill .knob { position: absolute; top: -11px; width: 30px; height: 30px; margin-left: -15px; border-radius: 50%; background: radial-gradient(circle at 40% 35%, #e06060, #a52a2a); border: 3px solid #f3c9c9; box-shadow: 0 1px 3px rgba(0,0,0,.3); }
  .skill .pct { position: absolute; top: 26px; width: 60px; margin-left: -30px; text-align: center; font: 400 16px "Poppins", sans-serif; color: var(--ink-soft); }

  .pro-card { width: 200px; height: 200px; border-radius: 50%; border: 5px solid var(--ring); text-align: center; font-family: "Poppins", sans-serif; }
  .pro-card.featured { border-color: var(--red); }
  .pro-card .badge { position: absolute; left: 61px; top: -59px; width: 68px; height: 68px; border-radius: 50%; background: var(--dark-badge); display: flex; align-items: center; justify-content: center; }
  .pro-card.featured .badge { background: var(--red); }
  .pro-card h5 { margin-top: 66px; font-size: 17px; font-weight: 600; color: var(--ink); }
  .pro-card p { margin-top: 8px; font-size: 15px; line-height: 22px; color: var(--ink-soft); }

  .footer-shape { left: 112px; top: 2122px; }
  .footer-title { left: 0; width: 1200px; top: 2196px; text-align: center; font: 700 28px "Poppins", sans-serif; color: var(--white); }
  .footer-rule { left: 112px; top: 2271px; width: 976px; height: 1px; background: rgba(255,255,255,.25); }
  .copyright { left: 0; width: 1200px; top: 2292px; text-align: center; font: 500 13.5px "Poppins", sans-serif; color: var(--white); }
  .footer-code { right: 156px; top: 2292px; font: 500 13.5px "Poppins", sans-serif; color: var(--white); }
</style>
</head>
<body>

<div class="abs top-band"></div>

<header>
  <div class="abs site-logo">VELMOT BV</div>
  <ul class="abs main-nav">
    <li>HOME</li><li>PORTFOLIO</li><li>PAGES</li><li>BLOG</li><li>CONTACT</li>
  </ul>
</header>

<section class="profile-hero">
  <div class="abs hero-panel"></div>
  <svg class="abs hero-chevron" width="976" height="98" viewBox="0 0 976 98">
    <polygon points="0,0 976,0 976,3 488,93 0,3" fill="#d24d4d"/>
    <polyline points="0,5 488,94 976,5" fill="none" stroke="#5a0505" stroke-width="5"/>
  </svg>

  <div class="abs portrait" role="img" aria-label="Portrait photo of Annie"></div>

  <div class="abs profile-toggle"><span class="off">Frank</span><span class="on">Annie</span></div>

  <div class="abs profile-info">
    <p class="name"><b>Name:</b> Annie</p>
    <p class="jobs-title">Actual Jobs:</p>
    <p class="job"><b>Director Veldterra:</b> Nemo enim ipsam voluptatem quia voluptas sit aspernatur aut odit.</p>
    <p class="job"><b>Netrin:</b> Nemo enim ipsam voluptatem quia voluptas sit aspernatur aut odit.</p>
  </div>

  <ul class="abs social-list" aria-label="Social profiles">
    <li><i></i></li><li><i></i></li><li><i></i></li><li><i></i></li><li><i></i></li>
  </ul>
</section>

<section class="about">
  <h2 class="abs section-title about-title">ABOUT ME</h2>
  <p class="abs about-text">Nemo enim ipsam voluptatem quia voluptas sit aspernatur aut odit aut fugit, sed quia consequuntur magni dolores eos qui ratione voluptatem sequi nesciunt. Neque porro quisquam est, qui dolorem ipsum quia dolor sit amet, consectetur, adipisci velit, sed quia non numquam eius modi tempora incidunt ut labore et dolore magnam.</p>
  <div class="abs read-more">Read More</div>

  <div class="abs finished-jobs">
    <div class="item"><h4><em>Finished Jobs:</em> Director Nordgas</h4><p>Sed ut perspiciatis unde omnis iste natus</p></div>
    <div class="item"><h4>Advisor Gas</h4><p>Sed ut perspiciatis unde omnis iste natus</p></div>
    <div class="item"><h4>Neque Quisquam</h4><p>Sed ut perspiciatis unde omnis iste natus</p></div>
  </div>
</section>

<div class="abs rule" style="top:1044px"></div>

<section class="skills">
  <h2 class="abs section-title centered-title" style="top:1102px">MY SKILLS</h2>

  <div class="abs skill" style="left:112px;top:1192px"><div class="label">General Management</div><div class="track"><div class="fill" style="width:80%"></div><span class="knob" style="left:80%"></span><span class="pct" style="left:80%">90%</span></div></div>
  <div class="abs skill" style="left:631px;top:1192px"><div class="label">Project Management</div><div class="track"><div class="fill" style="width:80%"></div><span class="knob" style="left:80%"></span><span class="pct" style="left:80%">90%</span></div></div>

  <div class="abs skill" style="left:112px;top:1295px"><div class="label">Energy Knowledge</div><div class="track"><div class="fill" style="width:70%"></div><span class="knob" style="left:70%"></span><span class="pct" style="left:70%">80%</span></div></div>
  <div class="abs skill" style="left:631px;top:1295px"><div class="label">Team Player</div><div class="track"><div class="fill" style="width:70%"></div><span class="knob" style="left:70%"></span><span class="pct" style="left:70%">80%</span></div></div>

  <div class="abs skill" style="left:112px;top:1398px"><div class="label">Gas Knowledge</div><div class="track"><div class="fill" style="width:98%"></div><span class="knob" style="left:98%"></span><span class="pct" style="left:98%">100%</span></div></div>
  <div class="abs skill" style="left:631px;top:1398px"><div class="label">Trouble Shooter</div><div class="track"><div class="fill" style="width:98%"></div><span class="knob" style="left:98%"></span><span class="pct" style="left:98%">100%</span></div></div>

  <div class="abs skill" style="left:112px;top:1501px"><div class="label">People Management</div><div class="track"><div class="fill" style="width:62%"></div><span class="knob" style="left:62%"></span><span class="pct" style="left:62%">70%</span></div></div>
  <div class="abs skill" style="left:631px;top:1501px"><div class="label">ETC</div><div class="track"><div class="fill" style="width:62%"></div><span class="knob" style="left:62%"></span><span class="pct" style="left:62%">70%</span></div></div>
</section>

<div class="abs rule" style="top:1671px"></div>

<section class="pro-skills">
  <h2 class="abs section-title centered-title" style="top:1728px">PROFESSIONAL SKILLS</h2>

  <div class="abs pro-card" style="left:225px;top:1847px">
    <span class="badge"><svg width="34" height="34" viewBox="0 0 34 34" fill="none" stroke="#fff" stroke-width="2"><rect x="5" y="5" width="18" height="24" rx="2"/><line x1="9" y1="11" x2="19" y2="11"/><line x1="9" y1="16" x2="16" y2="16"/><path d="M29 10 L18 24 L16 28 L20 26 L31 12 Z"/></svg></span>
    <h5>EDUCATION</h5><p>UVN<br>Atheneum B</p>
  </div>

  <div class="abs pro-card featured" style="left:500px;top:1847px">
    <span class="badge"><svg width="34" height="34" viewBox="0 0 34 34" fill="none" stroke="#fff" stroke-width="2"><rect x="4" y="10" width="26" height="18" rx="2"/><path d="M12 10 V6 H22 V10"/><line x1="4" y1="17" x2="30" y2="17"/><rect x="15" y="15" width="4" height="5"/></svg></span>
    <h5>WORKED FOR</h5><p>Nordgas<br>UVN</p>
  </div>

  <div class="abs pro-card" style="left:784px;top:1847px">
    <span class="badge"><svg width="34" height="34" viewBox="0 0 34 34" fill="none" stroke="#fff" stroke-width="2"><path d="M17 9 C13 7 8 7 4 8 V27 C8 26 13 26 17 28 Z"/><path d="M17 9 C21 7 26 7 30 8 V27 C26 26 21 26 17 28 Z"/></svg></span>
    <h5>OTHER</h5><p>Reading</p>
  </div>
</section>

<footer>
  <svg class="abs footer-shape" width="976" height="210" viewBox="0 0 976 210">
    <polygon points="0,88 488,4 976,88 976,210 0,210" fill="#d24d4d"/>
    <polyline points="0,88 488,4 976,88" fill="none" stroke="#5a0505" stroke-width="6"/>
  </svg>
  <div class="abs footer-title">VELMOT BV</div>
  <div class="abs footer-rule"></div>
  <p class="abs copyright">Copyrights @ 2018 VELMOT BV. All Rights Reserved.</p>
  <span class="abs footer-code">C20</span>
</footer>

</body>
</html>
```